Meridel Physical Therapy Co Brochure

We need a brochure that underscores the advantages of our PT clinic. The brochure will be a 6 X 9 postcard (cardboard paper). We like the use of bullet points (since physicians have limited time), underscore our location, provide an introduction to our clinic, create a nice logo, and what separates us (see below). Most important is location, about us (separates us from competition), and the logo.

Please make sure to list our website as www.meridel-pt.example. Also include schedule your Physical Therapy session at www.meridel-pt.example or call 847-555-0162.

What Makes Us Different

One-on-One Treatments
Our commitment to you is that you will receive one-on-one attention from one of our staff members with a Doctorate of Physical Therapy. We will never double, triple, or quadruple book "your appointment slot." This ensures that you get one-on-one time with your Doctor of Physical Therapy, and you are not doing your exercises alone in the corner like at the hospital or at the corporate physical therapy clinics. If you are currently seeing a Physical Therapist that is leaving you alone to perform your exercises, to go and treat other patients or is double / triple booking your appointment, please give us call today!

State-of the-Art Equipment
Even though we are a small / local PT clinic, we still made the capital investment to have only the best equipment for you to use in our clinic. Our Doctor of Physical Therapy will guide you through an individually customized plan on treatment, based on your initial evaluation. Thereafter, we will provide Home Exercises that will normally be different than your clinic treatment program. If your current clinic is simply having you perform the Home Exercises in the clinic, please give us a call today!

Russian Speaking
We are one of the few Russian-speaking Physical Therapy clinics in the Chicagoland area. If Russian is your preferred language, please give us a call today!

Manual Therapy
We believe that manual therapy is an important element towards rehabilitation for many patients. Our doctors are highly trained in the approaches of manual therapy. If your current clinic does not believe in manual therapy, please give us a call today!

Friendly and Caring Staff

Flexible Hours

Convenient Location
Located at the corner of Tolliver Rd and Harrow Ln, in the same shopping plaza as the Bright Lane Car Wash and the Perkwell Bakery. We are directly across the street from the NKRA of Buffalo Grove.

What We Do
Diagnoses We Treat

At Meridel Physical Therapy, we treat a variety of diagnoses. Here is a list of some of the typical things we treat:

Neck and Back Pain
Shoulder Pain/Rotator Cuff Disorders/Bursitis
Hip Pain
Knee, Ankle, and Foot Pain/Sprains
Post-Operative Care for Orthopedic Surgery including Total Joint Replacement and Spine Surgery
Balance Deficits/Fall Prevention
General Strengthening
Tendinitis
Specialty Programs

Work Injury
Sports Medicine/Sports Performance
Motor Vehicle Accident/Whiplash
Post-Surgical Protocols

Welcome to
Meridel Physical Therapy Company
Meridel Physical Therapy will utilize both physical therapy and group strength and balance classes to achieve an effective long-term, meaningful lifestyle change toward renewed strength and active living. Our patients will follow a three-step system, which begins with the Physical Therapist initial evaluation, continues into a rehabilitative stage, and terminates with a personalized ongoing lifestyle wellness plan.

Our goal is to help our patients improve function, independence, and the quality of their life. We believe that age is just a number, and it does not define one’s ability. We want to encourage everyone to invest the time to increase their strength, physical activity level, and the quality of their body movements.
We are one of the few Russian-speaking Physical Therapy clinics in Chicagoland area. Doctors of Physical Therapy at Meridel Physical Therapy Co are dedicated to developing a treatment plan that is custom-designed and tailored to each patient’s pace and comfort level.

Location
2834 Harrow Ln
Buffalo Grove, IL 60014
Phone: (847) 555-0162
Fax: (847) 555-0189

Physical Therapists Owned and Managed clinic

Target Market(s)

geriatrics, orthopedic / sports medicine, and work / auto accident injury patients

Industry/Entity Type

Physical Therapy

Font styles to use
Serif

Requirements
Must have
• location of our clinic
• logo of our clinic
• Schedule an a session online via our website (www.meridel-pt.example) or by via
• phone 847 555 0162
• link to our temporary website - http://2740.rehabsitetmp.example/ (do not list it on the brochure)
Nice to have
• could mention that we will have outstanding equipment (Vel-tor machine, Ironmoor Core Glide system, Quelsonic Modalities, etc)
Should not have
• should be able to fit nicely on 6 X 9 Postcard (needs to be double sided!)

```html
<!DOCTYPE html>
<html lang="en">
<head>
<meta charset="utf-8">
<title>Meridel Physical Therapy Co – About Us</title>
<link rel="stylesheet" href="https://fonts.googleapis.com/css2?family=Montserrat:wght@800&family=Nunito:wght@400;800;900&display=swap">
<style>
  :root {
    --brand-blue: #4470b5;
    --brand-blue-dark: #3a62a6;
    --leaf-green: #a9c54d;
    --leaf-green-pale: #dbe7b0;
    --photo-light: #eef2f6;
    --photo-mid: #cfd9e2;
    --white: #ffffff;
  }
  * { margin: 0; padding: 0; box-sizing: border-box; }
  html, body { width: 1200px; height: 800px; overflow: hidden; background: var(--white); }
  .postcard {
    position: relative; width: 1200px; height: 800px; overflow: hidden;
    background: var(--white);
    font-family: "Nunito", "Trebuchet MS", sans-serif;
    color: var(--brand-blue);
  }
  .therapy-photo { position: absolute; left: 520px; top: 0; width: 680px; height: 300px; }
  .figure-art { position: absolute; left: 245px; top: 145px; width: 260px; height: 620px; }
  .about-shape { position: absolute; left: 0; top: 0; width: 1200px; height: 800px; }

  .brand { position: absolute; left: 40px; top: 70px; display: flex; align-items: center; gap: 12px; }
  .brand-dot { width: 26px; height: 26px; border-radius: 50%; background: var(--leaf-green); }
  .brand-name { font-weight: 800; font-size: 27px; line-height: 1.15; color: var(--brand-blue); width: 320px; }

  .founder { position: absolute; left: 37px; top: 196px; }
  .founder-role { font-size: 23px; font-weight: 400; }
  .founder-name { font-size: 31px; font-weight: 900; line-height: 1.1; }
  .founder-name small { font-size: 17px; font-weight: 800; }

  .equipment { position: absolute; left: 36px; top: 340px; list-style: none; }
  .equipment li { font-size: 29px; line-height: 37px; color: var(--leaf-green); }
  .equipment li::before { content: "•"; font-size: 20px; margin-right: 8px; vertical-align: 3px; }

  .contact { position: absolute; left: 37px; border-left: 6px solid var(--brand-blue); padding-left: 10px; }
  .contact-label { font-size: 23px; line-height: 26px; }
  .contact-value { font-size: 25px; font-weight: 900; line-height: 29px; }
  .contact-address { top: 548px; }
  .contact-phone { top: 650px; }
  .contact-web { top: 716px; }

  .about-title {
    position: absolute; left: 678px; top: 198px;
    font-family: "Montserrat", "Arial Black", sans-serif; font-weight: 800;
    font-size: 86px; letter-spacing: -1px; color: var(--brand-blue); line-height: 1;
  }
  .about-col { position: absolute; top: 305px; width: 306px; color: var(--white); font-size: 18.5px; line-height: 24.6px; }
  .about-col p + p { margin-top: 24.6px; }
  .about-col strong { font-weight: 900; }
  .about-col-left { left: 518px; }
  .about-col-right { left: 838px; width: 310px; }
</style>
</head>
<body>
<main class="postcard">
  <div class="therapy-photo" role="img" aria-label="Photo of a physical therapist bending a patient's knee on a treatment table"
       style="background: linear-gradient(135deg, var(--photo-mid) 0%, var(--photo-light) 55%, #e3ebf0 100%);"></div>

  <div class="figure-art" role="img" aria-label="Green silhouettes of a person moving from bent over to standing upright"
       style="background: linear-gradient(180deg, var(--leaf-green) 0%, var(--leaf-green-pale) 100%); border-radius: 120px 120px 40px 40px; opacity: .75;"></div>

  <svg class="about-shape" viewBox="0 0 1200 800" aria-hidden="true">
    <path d="M790 84 C 690 120 600 190 560 262 C 530 285 500 300 490 330 L 490 740 Q 490 763 513 763 L 1163 763 L 1163 318 Q 1163 292 1137 292 L 585 292 C 630 230 700 150 790 84 Z" fill="var(--brand-blue)"/>
  </svg>

  <div class="brand">
    <span class="brand-dot"></span>
    <span class="brand-name">Meridel Physical Therapy Co</span>
  </div>

  <div class="founder">
    <p class="founder-role">Founder &amp; Medical Director</p>
    <p class="founder-name">Dr. Lera Voss, <small>PT, DPT</small></p>
  </div>

  <ul class="equipment">
    <li>Vel-tor</li>
    <li>Lumora</li>
    <li>Core Glide</li>
    <li>Lymphedema Pump</li>
  </ul>

  <div class="contact contact-address">
    <p class="contact-label">Our Address</p>
    <p class="contact-value">2834 Harrow Ln<br>Buffalo Grove, IL 60014</p>
  </div>
  <div class="contact contact-phone">
    <p class="contact-label">Call Today</p>
    <p class="contact-value">(847) 555 0162</p>
  </div>
  <div class="contact contact-web">
    <p class="contact-label">Book online</p>
    <p class="contact-value">www.meridel-pt.example</p>
  </div>

  <h1 class="about-title">ABOUT US</h1>

  <div class="about-col about-col-left">
    <p>Meridel Physical Therapy will utilize both physical therapy and group strength and balance classes to achieve an effective long-term, meaningful lifestyle change toward renewed strength and active living. Our patients will follow a three-step system, which begins with the Physical Therapist <strong>initial evaluation,</strong> continues into a <strong>rehabilitative stage,</strong> and terminates with a personalized ongoing <strong>lifestyle wellness plan.</strong></p>
    <p>Our goal is to help our patients <strong>improve function, independence,</strong> and the <strong>quality</strong></p>
  </div>
  <div class="about-col about-col-right">
    <p><strong>of their life.</strong> We believe that age is just a number, and it does not define one’s ability. We want to encourage everyone to invest the time to increase their strength, physical activity level, and the quality of their body movements.</p>
    <p>We are one of the few <strong>Russian-speaking</strong> Physical Therapy clinics in Chicagoland area. Doctors of Physical Therapy at Meridel Physical Therapy Co are dedicated to developing a treatment plan that is <strong>custom-designed and tailored</strong> to each patient’s pace and comfort level.</p>
  </div>
</main>
</body>
</html>
```